Zenqo - revolutionary mobile payment

The app is a P2P money trasfert, without the using of credit card or bank circuits it can transfer electronic money from one person to another consumers simply and immediatelly.
You can use the color you want, but the message we need to transert to consumer is simplicity, safety and coolness.
In attach the logo of the company and the wireframe of thre page of the app.
The goal is to design the page of the app with a clear, simple and intuitive graphic.
Updates

I have upgrade the brief with important information and detail, many thanks

Target Market(s)

all the people

Industry/Entity Type

Credit Card

Requirements
Must have
• You have to design one icon for each button in the first page, (shop is: where to shop)
in the second one a new intuitive image (instead of the hand) that let the user to understand that with a simple swipe he can process the payment
Nice to have
• You can include or esxclude what you want or belive can improve user experience of the app
Should not have
• too much color, too much button or information

```html
<!DOCTYPE html>
<html lang="it">
<head>
<meta charset="utf-8">
<title>Zenqo – Movimenti</title>
<link rel="stylesheet" href="https://fonts.googleapis.com/css2?family=Questrial&family=Montserrat:wght@600;700&display=swap">
<style>
  :root {
    --page-bg: #c3c6cb;
    --screen-bg: #e4e5e8;
    --status-bg: #0c0c0e;
    --navy: #1c2c5e;
    --navy-deep: #14224c;
    --band-top: #6477a3;
    --band-bottom: #2b3c6e;
    --row-top: #3a4c80;
    --row-bottom: #27386a;
    --text-light: #ffffff;
    --text-dark: #1b1b1b;
    --report-red: #b31d24;
    --pockets-green: #21a33f;
    --photo-tone: #6d7f6a;
  }
  * { box-sizing: border-box; margin: 0; padding: 0; }
  html, body { width: 1200px; height: 1195px; overflow: hidden; }
  body {
    background: var(--page-bg);
    font-family: "Questrial", sans-serif;
    display: flex; align-items: center; justify-content: center;
  }
  .app-screen {
    position: relative;
    width: 600px; height: 1065px;
    background: var(--screen-bg);
    overflow: hidden;
    box-shadow: 0 10px 40px rgba(0,0,0,.18);
  }
  .status-bar {
    height: 36px; background: var(--status-bg); color: var(--text-light);
    display: flex; align-items: center; justify-content: space-between;
    padding: 0 14px; font-size: 17px;
  }
  .status-bar .time { font-family: "Montserrat", sans-serif; font-weight: 600; }
  .status-bar .battery { display: flex; align-items: center; gap: 6px; }
  .top-strip {
    height: 50px; background: #f3f4f6;
    display: flex; align-items: center; justify-content: flex-end; padding-right: 22px;
  }
  .brand {
    display: flex; align-items: center; gap: 8px;
    font-family: "Montserrat", sans-serif; font-weight: 700; font-size: 26px; color: var(--navy);
  }
  .brand-dot { width: 22px; height: 22px; border-radius: 50%; background: var(--navy); }
  .balance-band {
    position: absolute; left: 120px; right: 0; top: 86px; height: 140px;
    background: linear-gradient(180deg, var(--band-top), var(--band-bottom));
  }
  .balance {
    position: absolute; left: 110px; top: 30px; color: var(--text-light);
  }
  .balance-label { font-size: 22px; }
  .balance-value { font-family: "Montserrat", sans-serif; font-weight: 700; font-size: 44px; letter-spacing: 1px; }
  .avatar {
    position: absolute; right: 34px; top: 10px;
    width: 120px; height: 120px; border-radius: 50%;
    border: 5px solid #f2f2f2;
    background: radial-gradient(circle at 50% 45%, #b99a84, var(--photo-tone));
  }
  .settings {
    position: absolute; left: 0; top: 86px; width: 120px; height: 140px;
    background: #f3f4f6; display: flex; align-items: flex-end; justify-content: center; padding-bottom: 20px;
  }
  .back-panel {
    position: absolute; left: 0; top: 226px; width: 120px; height: 250px;
    background: var(--navy-deep); color: var(--text-light);
    display: flex; align-items: center; justify-content: center; font-size: 22px;
  }
  .period-select {
    position: absolute; right: 16px; top: 234px;
    background: var(--navy); color: var(--text-light);
    font-size: 14px; padding: 6px 12px; display: flex; gap: 14px; align-items: center;
  }
  .transactions {
    position: absolute; left: 140px; right: 16px; top: 280px;
    list-style: none; display: flex; flex-direction: column; gap: 8px;
  }
  .transaction {
    height: 62px; display: flex; align-items: center; gap: 18px; padding: 0 18px;
    background: linear-gradient(180deg, var(--row-top), var(--row-bottom));
    color: var(--text-light); box-shadow: 0 3px 6px rgba(0,0,0,.25);
  }
  .transaction .number { flex: 1; font-size: 21px; letter-spacing: .5px; }
  .transaction .amount { width: 70px; font-family: "Montserrat", sans-serif; font-weight: 700; font-size: 18px; }
  .actions {
    position: absolute; left: 20px; right: 20px; top: 880px;
    display: flex; gap: 30px;
  }
  .action {
    flex: 1; height: 92px; display: flex; align-items: center; justify-content: center;
    font-family: "Montserrat", sans-serif; font-weight: 700; font-size: 26px; color: var(--text-light);
    box-shadow: 0 4px 8px rgba(0,0,0,.25);
  }
  .action-report { background: var(--report-red); }
  .action-pockets { background: var(--pockets-green); }
</style>
</head>
<body>
<main class="app-screen">
  <header class="status-bar">
    <span class="carrier">●●●○○ VELA</span>
    <span class="time">4:21 PM</span>
    <span class="battery">22%
      <svg width="30" height="14" viewBox="0 0 30 14"><rect x="1" y="1" width="25" height="12" rx="2" fill="none" stroke="#fff" stroke-width="1.5"/><rect x="3" y="3" width="6" height="8" fill="#fff"/><rect x="27" y="4" width="2" height="6" fill="#fff"/></svg>
    </span>
  </header>

  <div class="top-strip">
    <div class="brand"><span class="brand-dot"></span>Zenqo</div>
  </div>

  <div class="settings">
    <svg width="34" height="34" viewBox="0 0 24 24" aria-label="Impostazioni"><path fill="#222" d="M19.4 13a7.5 7.5 0 0 0 0-2l2.1-1.6-2-3.5-2.5 1a7.3 7.3 0 0 0-1.7-1L15 3h-4l-.4 2.9a7.3 7.3 0 0 0-1.7 1l-2.5-1-2 3.5L6.6 11a7.5 7.5 0 0 0 0 2l-2.1 1.6 2 3.5 2.5-1a7.3 7.3 0 0 0 1.7 1L11 21h4l.4-2.9a7.3 7.3 0 0 0 1.7-1l2.5 1 2-3.5zM13 15.5a3.5 3.5 0 1 1 0-7 3.5 3.5 0 0 1 0 7z"/></svg>
  </div>

  <section class="balance-band">
    <div class="balance">
      <p class="balance-label">Il Tuo Saldo</p>
      <p class="balance-value">€106.82</p>
    </div>
    <div class="avatar" role="img" aria-label="Foto profilo dell'utente"></div>
  </section>

  <nav class="back-panel">‹ Indietro</nav>

  <div class="period-select">Ultimi 30 Giorni <span>⌄</span></div>

  <ul class="transactions">
    <li class="transaction"><svg class="home" width="26" height="24" viewBox="0 0 26 24"><path fill="#fff" d="M13 2 1 12h4v10h6v-6h4v6h6V12h4z"/></svg><span class="number">+39 310 555 0142</span><span class="amount">€ 1</span><svg width="16" height="18" viewBox="0 0 16 18"><path fill="#fff" d="M2 1l13 8-13 8z"/></svg></li>
    <li class="transaction"><svg class="home" width="26" height="24" viewBox="0 0 26 24"><path fill="#fff" d="M13 2 1 12h4v10h6v-6h4v6h6V12h4z"/></svg><span class="number">+39 310 555 0142</span><span class="amount">€ -1</span><svg width="16" height="18" viewBox="0 0 16 18"><path fill="#fff" d="M2 1l13 8-13 8z"/></svg></li>
    <li class="transaction"><svg class="home" width="26" height="24" viewBox="0 0 26 24"><path fill="#fff" d="M13 2 1 12h4v10h6v-6h4v6h6V12h4z"/></svg><span class="number">+39 020 555 0187</span><span class="amount">€ 200</span><svg width="16" height="18" viewBox="0 0 16 18"><path fill="#fff" d="M2 1l13 8-13 8z"/></svg></li>
    <li class="transaction"><svg class="home" width="26" height="24" viewBox="0 0 26 24"><path fill="#fff" d="M13 2 1 12h4v10h6v-6h4v6h6V12h4z"/></svg><span class="number">+39 550 555 0163</span><span class="amount">€ 12</span><svg width="16" height="18" viewBox="0 0 16 18"><path fill="#fff" d="M2 1l13 8-13 8z"/></svg></li>
    <li class="transaction"><svg class="home" width="26" height="24" viewBox="0 0 26 24"><path fill="#fff" d="M13 2 1 12h4v10h6v-6h4v6h6V12h4z"/></svg><span class="number">+39 310 555 0142</span><span class="amount">€ -1</span><svg width="16" height="18" viewBox="0 0 16 18"><path fill="#fff" d="M2 1l13 8-13 8z"/></svg></li>
    <li class="transaction"><svg class="home" width="26" height="24" viewBox="0 0 26 24"><path fill="#fff" d="M13 2 1 12h4v10h6v-6h4v6h6V12h4z"/></svg><span class="number">+39 020 555 0187</span><span class="amount">€ 200</span><svg width="16" height="18" viewBox="0 0 16 18"><path fill="#fff" d="M2 1l13 8-13 8z"/></svg></li>
    <li class="transaction"><svg class="home" width="26" height="24" viewBox="0 0 26 24"><path fill="#fff" d="M13 2 1 12h4v10h6v-6h4v6h6V12h4z"/></svg><span class="number">+39 550 555 0163</span><span class="amount">€ 12</span><svg width="16" height="18" viewBox="0 0 16 18"><path fill="#fff" d="M2 1l13 8-13 8z"/></svg></li>
  </ul>

  <div class="actions">
    <a class="action action-report">Report</a>
    <a class="action action-pockets">Tasche</a>
  </div>
</main>
</body>
</html>
```